Calm Nest

I currently have a squarespace website www.bodysensepillow.comI want a complete design change but I want you to use the current information on the site.
Updates

We will be making a decision this week. Thank You.

```html
<!DOCTYPE html>
<html lang="en">
<head>
<meta charset="utf-8">
<title>Calm Nest</title>
<link rel="stylesheet" href="https://fonts.googleapis.com/css2?family=Roboto:wght@400;500;700&family=Open+Sans:wght@400;600&family=Great+Vibes&display=swap">
<style>
:root{
  --navy:#1b5f9e;
  --sky:#2aa6de;
  --button:#3aa8dc;
  --mint:#2ecc9a;
  --label-blue:#1f6fae;
  --ink:#333a40;
  --muted:#5d6670;
  --rule:#c9d3dc;
  --footer:#1c1d1f;
  --white:#ffffff;
}
*{margin:0;padding:0;box-sizing:border-box}
html,body{width:1200px;height:4749px;overflow:hidden;background:var(--white)}
body{position:relative;font-family:"Open Sans",Arial,sans-serif;color:var(--ink)}
.abs{position:absolute}
.photo{position:absolute}
.btn{position:absolute;display:flex;align-items:center;justify-content:center;border-radius:30px;background:var(--button);color:var(--white);font:700 18px "Roboto",sans-serif;box-shadow:0 4px 10px rgba(0,0,0,.12)}
.btn-outline{background:var(--white);color:var(--navy);border:2px solid var(--navy);box-shadow:none}
.section-title{position:absolute;display:flex;align-items:center;gap:22px;font:700 34px "Roboto",sans-serif;color:var(--navy);letter-spacing:.5px}
.section-title::before,.section-title::after{content:"";width:70px;height:2px;background:var(--rule)}
.section-title .accent{color:var(--sky)}
.script{position:absolute;font-family:"Great Vibes",cursive;color:var(--ink);text-align:center}
.banner-sub{position:absolute;text-align:center;font-family:"Roboto",sans-serif;color:var(--ink)}
.card{position:absolute;overflow:hidden;border-radius:6px;box-shadow:0 8px 22px rgba(0,0,0,.18)}
.card-label{position:absolute;left:0;bottom:0;height:72px;width:250px;display:flex;align-items:center;padding-left:22px;color:var(--white);font:700 22px "Roboto",sans-serif;clip-path:polygon(0 0,78% 0,100% 100%,0 100%)}
.label-mint{background:var(--mint)}
.label-blue{background:var(--label-blue)}
.field{position:absolute;border:1.5px solid #c7cdd3;border-radius:4px;padding:10px 14px;font:400 17px "Open Sans",sans-serif;color:var(--ink);background:var(--white)}
.foot-head{position:absolute;font:700 15px "Roboto",sans-serif;color:var(--sky);letter-spacing:.5px}
.foot-list{position:absolute;list-style:none;font:400 14px "Open Sans",sans-serif;color:#c9ced3;line-height:22px}
.foot-rule{position:absolute;height:1px;background:#4a4d52}
</style>
</head>
<body>

<!-- Hero -->
<div class="photo" role="img" aria-label="Photo of a smiling woman lying on striped bedding and pillows" style="left:0;top:0;width:1200px;height:690px;background:linear-gradient(100deg,#e9e7e2 0%,#d8d6d0 35%,#c9bfb4 60%,#a58d78 72%,#e6e4df 100%)"></div>
<svg class="abs" style="left:0;top:580px" width="1200" height="120" viewBox="0 0 1200 120" aria-hidden="true">
  <path d="M0 110 C 400 110 800 90 1200 20 L1200 120 L0 120 Z" fill="#ffffff"/>
</svg>

<header>
  <div class="abs" style="left:47px;top:58px;font:500 46px 'Roboto',sans-serif;color:var(--sky)">Calm Nest</div>
  <nav class="abs" style="left:434px;top:74px;display:flex;gap:30px;font:700 15px 'Roboto',sans-serif;color:var(--ink)">
    <span style="color:var(--mint)">HOME</span>
    <span>COMPANY ▾</span>
    <span>PILLOWS ▾</span>
    <span>SHEETS ▾</span>
    <span>NEW COLLECTION 2019</span>
    <span>CONTACT</span>
  </nav>
  <svg class="abs" style="left:1136px;top:70px" width="26" height="26" viewBox="0 0 26 26" aria-label="Search">
    <circle cx="11" cy="11" r="8" fill="none" stroke="#333a40" stroke-width="3"/>
    <line x1="17" y1="17" x2="24" y2="24" stroke="#333a40" stroke-width="3" stroke-linecap="round"/>
  </svg>
</header>

<h1 class="abs" style="left:85px;top:328px;width:620px;font:700 38px/46px 'Roboto',sans-serif;color:var(--ink)">Helping people sleep better is the most important thing that we do</h1>
<div class="btn" style="left:85px;top:446px;width:285px;height:54px">Learn More</div>

<!-- About -->
<h2 class="section-title" style="left:95px;top:782px">ABOUT <span class="accent">US</span></h2>
<p class="abs" style="left:95px;top:866px;width:620px;font:400 16px/23px 'Open Sans',sans-serif;color:var(--ink)">Calm Nest believes that sleep is the most important part of your life. We created Calm Nest because better sleep makes for a better life. We carry a variety of speciality sleep products that are made with the finest materials available. Our aim is to offer you the best-made sheets possible–more sumptuous, more durable, and more exquisite than anything else available. Sheets are essential in helping one sleep well at night.</p>
<div class="btn btn-outline" style="left:95px;top:1065px;width:237px;height:46px">Learn More</div>
<div class="abs" style="left:770px;top:780px;width:340px;height:340px;border-radius:50%;background:#fff;box-shadow:0 4px 18px rgba(0,0,0,.12)"></div>
<div class="photo" role="img" aria-label="Photo of a family lying together on a bed" style="left:790px;top:800px;width:300px;height:300px;border-radius:50%;background:linear-gradient(160deg,#d9c3ad,#a46a4e 55%,#e7e4df)"></div>

<!-- Sustainable banner -->
<div class="photo" role="img" aria-label="Photo of a woman resting on a white pillow in a bright bedroom" style="left:0;top:1203px;width:1200px;height:418px;background:linear-gradient(90deg,#cfcfcd 0%,#e4e2de 30%,#d8c4b2 48%,#f1f0ee 65%,#f7f7f6 100%)"></div>
<div class="script" style="left:680px;top:1262px;width:380px;font-size:66px">Sustainable</div>
<div class="banner-sub" style="left:700px;top:1386px;width:340px;font-size:23px;padding-bottom:10px;border-bottom:1.5px solid #9aa0a6">Squeezable and Supportive</div>
<div class="banner-sub" style="left:700px;top:1432px;width:340px;font-size:14px;line-height:18px">Our eco-conscious materials &amp; cooling comfort design will change your sleep for the better</div>
<div class="btn" style="left:753px;top:1507px;width:241px;height:48px">Discover More</div>

<!-- Pillows -->
<h2 class="section-title" style="left:430px;top:1695px">PILLOWS</h2>
<svg class="abs" style="left:72px;top:1914px" width="22" height="34" viewBox="0 0 22 34" aria-label="Previous"><path d="M17 4 L5 17 L17 30" fill="none" stroke="#555" stroke-width="4"/></svg>
<svg class="abs" style="left:1104px;top:1914px" width="22" height="34" viewBox="0 0 22 34" aria-label="Next"><path d="M5 4 L17 17 L5 30" fill="none" stroke="#555" stroke-width="4"/></svg>
<div class="card" style="left:127px;top:1782px;width:453px;height:298px">
  <div class="photo" role="img" aria-label="Photo of two blue pillows on a striped bed" style="inset:0;background:linear-gradient(180deg,#d7c8b4 0%,#b9a890 30%,#4fb6d8 45%,#6fc4e0 60%,#e7e4df 75%,#cfd2d3 100%)"></div>
  <div class="card-label label-mint">Breeze Fit®</div>
</div>
<div class="card" style="left:617px;top:1782px;width:453px;height:298px">
  <div class="photo" role="img" aria-label="Photo of stacked cream organic pillows" style="inset:0;background:linear-gradient(150deg,#f6f3ec 0%,#e9dfcc 45%,#d9cbb2 70%,#f3f0ea 100%)"></div>
  <div class="card-label label-mint">Pure Rest®</div>
</div>

<!-- Live well banner -->
<div class="photo" role="img" aria-label="Photo of a smiling woman holding striped bedding" style="left:0;top:2153px;width:1200px;height:418px;background:linear-gradient(90deg,#f3f3f2 0%,#e9e8e6 40%,#c6bcb0 62%,#6e5a4b 78%,#b9afa4 100%)"></div>
<div class="script" style="left:100px;top:2218px;width:520px;font-size:60px">Live Well Sleep Well</div>
<div class="banner-sub" style="left:160px;top:2320px;width:400px;font-size:23px;padding-bottom:10px;border-bottom:1.5px solid #9aa0a6">Custom Design, Private Label</div>
<div class="banner-sub" style="left:120px;top:2364px;width:480px;font-size:14px;line-height:18px">We custom design, private label and manufacture the highest grade sleep products in the industry at value prices.</div>
<div class="btn" style="left:231px;top:2444px;width:241px;height:48px">Discover More</div>

<!-- Sheets -->
<h2 class="section-title" style="left:445px;top:2645px">SHEETS</h2>
<div class="card" style="left:95px;top:2739px;width:485px;height:291px">
  <div class="photo" role="img" aria-label="Photo of a couple relaxing on bamboo sheets" style="inset:0;background:linear-gradient(160deg,#8c7a6a 0%,#d6c2ae 35%,#6d6f78 65%,#3f4350 100%)"></div>
  <div class="card-label label-blue">Bamboo</div>
</div>
<div class="card" style="left:617px;top:2739px;width:491px;height:291px">
  <div class="photo" role="img" aria-label="Photo of a child lying on white cool sheets" style="inset:0;background:linear-gradient(170deg,#c7cbc9 0%,#e7e9e8 40%,#f6f7f7 70%,#dfe3e4 100%)"></div>
  <div class="card-label label-blue">Cool</div>
</div>

<!-- New collection banner -->
<div class="photo" role="img" aria-label="Photo of a bed made with striped linen bedding and a round tray" style="left:0;top:3103px;width:1200px;height:506px;background:linear-gradient(160deg,#dcdcd8 0%,#c7c8c3 30%,#eeeeec 55%,#d5d3ce 80%,#f2f2f1 100%)"></div>
<div class="abs" style="left:560px;top:3240px;width:540px;height:1.5px;background:#8a9096"></div>
<div class="script" style="left:560px;top:3250px;width:540px;font-size:62px">New Collection 2019</div>
<div class="abs" style="left:560px;top:3340px;width:540px;height:1.5px;background:#8a9096"></div>
<div class="banner-sub" style="left:600px;top:3350px;width:460px;font-size:15px;line-height:19px">Check out our Copper Bamboo Performance Bedding, Pattern Linens and Cooling Performance Products</div>
<div class="btn" style="left:706px;top:3429px;width:244px;height:48px">Discover More</div>

<!-- Contact -->
<div class="abs" style="left:100px;top:3696px;width:320px;height:320px;border-radius:50%;background:#fff;box-shadow:0 4px 18px rgba(0,0,0,.15)"></div>
<div class="photo" role="img" aria-label="Photo of a couple sitting together on a bed" style="left:113px;top:3709px;width:294px;height:294px;border-radius:50%;background:linear-gradient(150deg,#c9b9a8,#8a6a55 50%,#3c3f47)"></div>
<h2 class="section-title" style="left:610px;top:3682px">CONTACT <span class="accent">US</span></h2>
<div class="field" style="left:513px;top:3777px;width:285px;height:48px">Your Name</div>
<div class="field" style="left:817px;top:3777px;width:291px;height:48px">Your Email</div>
<div class="field" style="left:513px;top:3840px;width:595px;height:133px">Message</div>
<div class="btn" style="left:690px;top:3986px;width:241px;height:46px">Submit</div>

<!-- Footer -->
<svg class="abs" style="left:0;top:4060px" width="1200" height="110" viewBox="0 0 1200 110" aria-hidden="true">
  <path d="M0 110 L0 90 C 450 90 850 70 1200 0 L1200 110 Z" fill="#1c1d1f"/>
</svg>
<footer class="abs" style="left:0;top:4168px;width:1200px;height:581px;background:var(--footer)">
  <div class="abs" style="left:0;top:86px;width:1200px;text-align:center;font:500 48px 'Roboto',sans-serif;color:var(--sky)">Calm Nest</div>
  <div class="abs" style="left:552px;top:190px;display:flex;gap:10px">
    <span style="width:26px;height:26px;border-radius:50%;border:1.5px solid #8d9298"></span>
    <span style="width:26px;height:26px;border-radius:50%;border:1.5px solid #8d9298"></span>
    <span style="width:26px;height:26px;border-radius:50%;border:1.5px solid #8d9298"></span>
  </div>

  <div class="foot-head" style="left:104px;top:264px">COMPANY</div>
  <div class="foot-rule" style="left:104px;top:290px;width:140px"></div>
  <ul class="foot-list" style="left:104px;top:302px"><li>About Us</li><li>Become a Retailer</li><li>Press</li></ul>

  <div class="foot-head" style="left:288px;top:264px">PILLOWS</div>
  <div class="foot-rule" style="left:288px;top:290px;width:140px"></div>
  <ul class="foot-list" style="left:288px;top:302px"><li>Breeze Fit®</li><li>Pure Rest®</li><li>Warm Rest™</li><li>Earth Rest®</li></ul>

  <div class="foot-head" style="left:475px;top:264px">SHEETS</div>
  <div class="foot-rule" style="left:475px;top:290px;width:90px"></div>
  <ul class="foot-list" style="left:475px;top:302px"><li>Bamboo</li><li>Cool</li></ul>

  <div class="foot-head" style="left:592px;top:264px">CONTACT</div>
  <div class="foot-rule" style="left:592px;top:290px;width:200px"></div>
  <svg class="abs" style="left:592px;top:302px" width="24" height="24" viewBox="0 0 24 24" aria-label="Address"><circle cx="12" cy="12" r="11" fill="none" stroke="#2ecc9a" stroke-width="1.5"/><path d="M12 6a4 4 0 0 0-4 4c0 3 4 8 4 8s4-5 4-8a4 4 0 0 0-4-4z" fill="#2ecc9a"/></svg>
  <ul class="foot-list" style="left:624px;top:302px"><li>Calm Nest Cushion</li><li>48 Sample Lane</li><li>Springfield, NY 10001</li></ul>
  <svg class="abs" style="left:592px;top:396px" width="24" height="24" viewBox="0 0 24 24" aria-label="Phone"><circle cx="12" cy="12" r="11" fill="none" stroke="#2ecc9a" stroke-width="1.5"/><path d="M8 7l2 0 1 3-1.5 1a7 7 0 0 0 3.5 3.5l1-1.5 3 1 0 2a2 2 0 0 1-2 1A9 9 0 0 1 6 9a2 2 0 0 1 2-2z" fill="#2ecc9a"/></svg>
  <ul class="foot-list" style="left:624px;top:397px"><li>555.010.0199</li></ul>
  <svg class="abs" style="left:592px;top:438px" width="24" height="24" viewBox="0 0 24 24" aria-label="Email"><circle cx="12" cy="12" r="11" fill="none" stroke="#2ecc9a" stroke-width="1.5"/><rect x="6.5" y="8" width="11" height="8" fill="none" stroke="#2ecc9a" stroke-width="1.5"/><path d="M6.5 8l5.5 4.5L17.5 8" fill="none" stroke="#2ecc9a" stroke-width="1.5"/></svg>
  <ul class="foot-list" style="left:624px;top:439px"><li>info@calmnest.example</li></ul>

  <div class="foot-head" style="left:839px;top:264px">NEWSLETTER</div>
  <div class="foot-rule" style="left:839px;top:290px;width:262px"></div>
  <p class="abs" style="left:839px;top:302px;width:262px;font:400 14px/20px 'Open Sans',sans-serif;color:#c9ced3">Register your email address to get more information about us.</p>
  <div class="abs" style="left:839px;top:352px;width:262px;height:34px;border-radius:17px;background:#fff;padding:7px 16px;font:400 14px 'Open Sans',sans-serif;color:var(--ink)">Email Address</div>
  <div class="abs" style="left:839px;top:396px;width:110px;height:30px;border-radius:15px;background:var(--label-blue);color:#fff;font:700 12px/30px 'Roboto',sans-serif;text-align:center">SUBSCRIBE</div>

  <div class="abs" style="left:0;top:527px;width:1200px;height:54px;background:#f4f4f4;text-align:center;font:600 12px/54px 'Open Sans',sans-serif;color:var(--ink)">COPYRIGHT © 2019 CALM NEST. ALL RIGHTS RESERVED.</div>
</footer>

</body>
</html>
```